Quillmarsh Property Solutions need a business card design

Hello guys. We would need a business card design asap please.
We are a start up property investment business based in London UK specialised in buying, selling, managing and letting properties and helping distressed property owners.
The name of our Business is Quillmarsh, the logo symbolises the four fundamental elements of the world (earth, air, fire and water) and so it stands for strength, stability, longevity.
We would like the business card to communicate professionalism and reliability. Many many thanks indeed for your work.

Details:

1.) Rosalind Updike
Property Investor
Mobile: +44(0)7700123456
Email: rosalind.quillmarsh@mailbox-example.com

2.) Dominic Updike
Property Investor
Mobile: +44(0)7700987654
Email: dominic.quillmarsh@mailbox-example.com

```html
<!DOCTYPE html>
<html lang="en">
<head>
<meta charset="utf-8">
<title>Quillmarsh Property Solutions – Business Card</title>
<link rel="stylesheet" href="https://fonts.googleapis.com/css2?family=Aldrich&family=Play:wght@400;700&display=swap">
<style>
  :root {
    --page: #ecebe8;
    --card-white: #ffffff;
    --blue: #3f8fe6;
    --blue-deep: #2f78d2;
    --ink: #1e2630;
    --accent-blue: #4a9be8;
    --rule-green: #1f8a4a;
    --muted: #3a4450;
  }
  html, body {
    margin: 0;
    width: 1200px;
    height: 1020px;
    overflow: hidden;
    background: var(--page);
  }
  .canvas {
    position: relative;
    width: 1200px;
    height: 1020px;
  }
  .card {
    position: absolute;
    left: 200px;
    width: 800px;
    height: 457px;
    background: var(--card-white);
    box-shadow: 0 6px 22px rgba(0,0,0,0.14);
    overflow: hidden;
  }
  .card--front { top: 40px; }
  .card--back { top: 523px; }
  .card__art {
    position: absolute;
    inset: 0;
    width: 100%;
    height: 100%;
  }
  .brand {
    position: absolute;
    left: 62px;
    top: 70px;
    display: flex;
    align-items: center;
    gap: 14px;
  }
  .brand__dot {
    width: 26px;
    height: 26px;
    border-radius: 50%;
    background: var(--blue);
  }
  .brand__name {
    font-family: "Aldrich", sans-serif;
    font-size: 26px;
    letter-spacing: 2px;
    color: var(--ink);
  }
  .identity {
    position: absolute;
    left: 62px;
    top: 180px;
  }
  .identity__role {
    font-family: "Aldrich", sans-serif;
    font-size: 17px;
    letter-spacing: 2px;
    color: var(--accent-blue);
    text-transform: uppercase;
  }
  .identity__name {
    font-family: "Aldrich", sans-serif;
    font-size: 38px;
    letter-spacing: 1px;
    color: var(--ink);
    text-transform: uppercase;
    line-height: 1.1;
    margin-top: 4px;
    white-space: nowrap;
  }
  .identity__rule {
    width: 360px;
    height: 3px;
    background: var(--rule-green);
    margin-top: 10px;
  }
  .contact {
    position: absolute;
    left: 62px;
    top: 290px;
    margin: 0;
    padding: 0;
    list-style: none;
    font-family: "Play", sans-serif;
    font-size: 17px;
    color: var(--muted);
  }
  .contact__item {
    display: flex;
    align-items: center;
    gap: 12px;
    height: 32px;
    white-space: nowrap;
  }
  .contact__item--address { text-transform: uppercase; }
  .contact__icon {
    width: 16px;
    height: 16px;
    fill: var(--blue-deep);
    flex: none;
  }
</style>
</head>
<body>
<main class="canvas">

  <section class="card card--front" aria-label="Business card front">
    <svg class="card__art" viewBox="0 0 800 457" aria-hidden="true">
      <defs>
        <radialGradient id="front-glow" cx="0.6" cy="0.3" r="0.8">
          <stop offset="0" stop-color="#8cc2f6"/>
          <stop offset="1" stop-color="#3a89e2"/>
        </radialGradient>
      </defs>
      <polygon points="470,0 800,0 800,457 560,457" fill="url(#front-glow)"/>
      <polygon points="500,0 800,0 800,457 610,457 690,230" fill="#5aa3ee" opacity="0.55"/>
      <polygon points="540,0 800,0 800,457 660,457 730,230" fill="#4a97ea" opacity="0.55"/>
      <polygon points="580,0 800,0 800,457 710,457 770,230" fill="#3a88e0" opacity="0.5"/>
    </svg>

    <div class="brand">
      <span class="brand__dot"></span>
      <span class="brand__name">QUILLMARSH</span>
    </div>

    <div class="identity">
      <div class="identity__role">Property Investor</div>
      <div class="identity__name">Rosalind Updike</div>
      <div class="identity__rule"></div>
    </div>

    <ul class="contact">
      <li class="contact__item">
        <svg class="contact__icon" viewBox="0 0 16 16"><path d="M3 1l3 3-1.5 2a9 9 0 005.5 5.5L12 10l3 3-2 2C6 14 2 10 1 3z"/></svg>
        <span>+44(0)7700123456</span>
      </li>
      <li class="contact__item">
        <svg class="contact__icon" viewBox="0 0 16 16"><path d="M1 3h14v10H1z M1 3l7 6 7-6" fill="none" stroke="#2f78d2" stroke-width="1.6"/></svg>
        <span>rosalind.quillmarsh@mailbox-example.com</span>
      </li>
      <li class="contact__item">
        <svg class="contact__icon" viewBox="0 0 16 16"><circle cx="8" cy="8" r="6.5" fill="none" stroke="#2f78d2" stroke-width="1.6"/><path d="M1.5 8h13M8 1.5c-3 3-3 10 0 13M8 1.5c3 3 3 10 0 13" fill="none" stroke="#2f78d2" stroke-width="1.2"/></svg>
        <span>www.quillmarsh-example.com</span>
      </li>
      <li class="contact__item contact__item--address">
        <svg class="contact__icon" viewBox="0 0 16 16"><path d="M8 1a5 5 0 015 5c0 4-5 9-5 9S3 10 3 6a5 5 0 015-5zm0 3a2 2 0 100 4 2 2 0 000-4z"/></svg>
        <span>12 Harrow Lane, London E1 6AN</span>
      </li>
    </ul>
  </section>

  <section class="card card--back" aria-label="Business card back">
    <svg class="card__art" viewBox="0 0 800 457" aria-hidden="true">
      <defs>
        <radialGradient id="back-glow" cx="0.45" cy="0.3" r="0.85">
          <stop offset="0" stop-color="#8cc2f6"/>
          <stop offset="1" stop-color="#3a89e2"/>
        </radialGradient>
      </defs>
      <rect width="800" height="457" fill="url(#back-glow)"/>
      <polygon points="0,0 220,0 300,260 0,457" fill="#5aa3ee" opacity="0.45"/>
      <polygon points="0,0 170,0 250,280 0,457" fill="#4a97ea" opacity="0.45"/>
      <polygon points="0,0 120,0 200,300 0,457" fill="#3a88e0" opacity="0.45"/>
      <polygon points="0,330 420,330 800,457 0,457" fill="#ffffff"/>
    </svg>
  </section>

</main>
</body>
</html>
```